Local fast-growing company in the service sector

We are looking for a modern business card design, which should also appear on our letterheads

Target Market(s)

Private and industrial sectors

Contact Information for Business Card

Vorname Name
Kellberger Str. 18
74523 Lindenfeld
Tel.: 07146-839214-0
Name@agentur-kvtl.de

Colors
9d9d9d
919191
aaaaaa

Requirements
Must have
• The logo (file) in silver

```html
<!DOCTYPE html>
<html lang="de">
<head>
<meta charset="utf-8">
<title>KVTL Visitenkarte</title>
<link rel="stylesheet" href="https://fonts.googleapis.com/css2?family=Michroma&family=Varela+Round&display=swap">
<style>
  :root {
    --page-bg: #d6d6d4;
    --card-bg: #ececea;
    --panel-dark: #2e2e2e;
    --panel-dark-edge: #3b3b3b;
    --ink: #2a2a2a;
    --silver: #aaaaaa;
    --silver-dim: #919191;
  }
  html, body {
    margin: 0;
    width: 1200px;
    height: 1010px;
    overflow: hidden;
    background: var(--page-bg);
  }
  .business-card {
    position: absolute;
    left: 173px;
    top: 281px;
    width: 853px;
    height: 495px;
    background: var(--card-bg);
    box-shadow: 0 16px 36px rgba(0,0,0,0.18);
    overflow: hidden;
  }
  .card-shapes {
    position: absolute;
    inset: 0;
  }
  .holder-name {
    position: absolute;
    left: 43px;
    top: 60px;
    margin: 0;
    font-family: "Michroma", sans-serif;
    font-size: 23px;
    line-height: 30px;
    letter-spacing: 1px;
    font-weight: 400;
    color: var(--ink);
    white-space: nowrap;
  }
  .contact-block {
    position: absolute;
    left: 43px;
    top: 342px;
    margin: 0;
    font-family: "Varela Round", sans-serif;
    font-size: 19px;
    line-height: 29px;
    color: var(--ink);
    font-style: normal;
    white-space: nowrap;
  }
  .contact-line {
    display: flex;
    align-items: center;
    gap: 18px;
  }
  .contact-icon {
    width: 18px;
    height: 15px;
    fill: var(--ink);
  }
  .brand-lockup {
    position: absolute;
    left: 640px;
    top: 247px;
    transform: translate(-50%, -50%);
    text-align: center;
    font-family: "Varela Round", sans-serif;
    white-space: nowrap;
  }
  .brand-name {
    display: block;
    font-size: 62px;
    line-height: 1;
    letter-spacing: 3px;
    color: var(--silver);
  }
  .brand-web {
    display: block;
    margin-top: 4px;
    font-size: 20px;
    letter-spacing: 1px;
    color: var(--silver-dim);
  }
</style>
</head>
<body>
  <section class="business-card">
    <svg class="card-shapes" viewBox="0 0 853 495" width="853" height="495" aria-hidden="true">
      <defs>
        <linearGradient id="panelShade" x1="0" y1="0" x2="1" y2="1">
          <stop offset="0" stop-color="var(--panel-dark-edge)"/>
          <stop offset="1" stop-color="var(--panel-dark)"/>
        </linearGradient>
      </defs>
      <path class="accent-arc" d="M460 4 Q317 245 450 491" fill="none" stroke="var(--panel-dark)" stroke-width="6" stroke-linecap="round"/>
      <path class="brand-panel" d="M475 0 Q342 245 462 495 L853 495 L853 0 Z" fill="url(#panelShade)"/>
    </svg>

    <h1 class="holder-name">VORNAME NAME</h1>

    <address class="contact-block">
      <div>Kellberger Str. 18</div>
      <div>74523 Lindenfeld</div>
      <div class="contact-line">
        <svg class="contact-icon" viewBox="0 0 22 18"><path d="M2 5 Q11 -1 20 5 L17 8 L14 6 L8 6 L5 8 Z M5 9 H17 L19 17 H3 Z"/></svg>
        <span>07146-839214-0</span>
      </div>
      <div class="contact-line">
        <svg class="contact-icon" viewBox="0 0 22 18"><path d="M2 3 H20 L11 10 Z M2 5 L11 12 L20 5 V15 H2 Z"/></svg>
        <span>Name@agentur-kvtl.de</span>
      </div>
    </address>

    <div class="brand-lockup">
      <span class="brand-name">KVTL</span>
      <span class="brand-web">agentur-kvtl.de</span>
    </div>
  </section>
</body>
</html>
```